Brevard Trade Partners - we are Asian sourcing agents

We are sourcing agents based in the USA and we act as sourcing agents for clients in throughout the world. We focus primarily on custom sewn goods. So basically companies who do not have the in-house expertise to do it themselves, come to us and have us find suitable factories in Asia to do the production. We are middlemen. We find the factories...quote the project...manage the quality control and then deliver the goods directly to our customer's door. We pride ourselves in making the communication very easy and precise.

Current page is www.brevardtradepartners.com

I am not happy w/ the overall look. The spacing...the photos, the fonts...the design elements...the pictures. I want a cool, crisp design that conveys professionalism and clearly depicts/explains what we do.

Requirements
Must have
• use my logo....I like it...it was designed by someone on this website.
Nice to have
• a video/animation of the entire process would be wonderful. Showing initial contact with our office in the USA...then to my correspondence with my offices in Taiwan and in Hong Kong...and then back and fort w/ the customer.....and then between my people in Hong Kong/Taiwan with the local factories......and then a quote is generated and sent to my client......to samples being made and sent for approval.....to a PO being generated......to final samples being sent.....to the order being shipped and delivered to the clients warehouse. I was thinking of an animation showing arrows and text showing the back and forth communication and explaining how the process flows.

```html
<!DOCTYPE html>
<html lang="en">
<head>
<meta charset="utf-8">
<title>Brevard Trade Partners</title>
<link href="https://fonts.googleapis.com/css2?family=Open+Sans:wdth,wght@75..100,300..800&display=swap" rel="stylesheet">
<style>
  :root {
    --green: #789414;
    --green-text: #6f8b12;
    --navy: #1b2f6b;
    --ink: #111111;
    --body: #4a4a4a;
    --panel: #f5f5f5;
    --nav-panel: #ededed;
    --dark: #121212;
    --dark-2: #1e1e1e;
    --white: #ffffff;
  }
  * { margin: 0; padding: 0; box-sizing: border-box; }
  html, body { width: 1200px; height: 1166px; overflow: hidden; }
  body { position: relative; font-family: "Open Sans", Arial, sans-serif; color: var(--body); background: #dfe6ee; }
  .cond { font-stretch: 75%; font-weight: 700; }

  .backdrop-left, .backdrop-right { position: absolute; top: 0; height: 1166px; width: 190px; }
  .backdrop-left { left: 0; background: linear-gradient(180deg, #e9eef4 0%, #d3dce7 40%, #2a3a55 62%, #070a10 100%); }
  .backdrop-right { right: 0; background: linear-gradient(180deg, #eef2f6 0%, #cfd9e5 45%, #344a6d 70%, #1b2a45 100%); }

  .page { position: absolute; left: 190px; top: 0; width: 820px; height: 1166px; }

  .masthead { position: absolute; left: 0; top: 0; width: 820px; height: 385px; }
  .nav-panel { position: absolute; left: 0; top: 0; width: 293px; height: 385px; background: var(--nav-panel); }
  .brand { position: absolute; left: 34px; top: 34px; display: flex; align-items: center; gap: 8px; }
  .brand-dot { width: 40px; height: 40px; border-radius: 50%; background: var(--navy); }
  .brand-name { font-stretch: 75%; font-weight: 700; font-size: 20px; line-height: 20px; color: var(--navy); width: 180px; }
  .main-nav { position: absolute; left: 41px; top: 122px; list-style: none; }
  .main-nav li { font-size: 14px; line-height: 29px; color: var(--ink); text-transform: uppercase; letter-spacing: .2px; }
  .hero { position: absolute; left: 293px; top: 0; width: 527px; height: 385px; background: linear-gradient(135deg, #f2f4f7 0%, #cfd8e2 25%, #1f8ae6 45%, #1a78d2 70%, #d9dee4 100%); }

  .toolbar { position: absolute; left: 0; top: 385px; width: 820px; height: 62px; background: var(--green); }
  .social { position: absolute; left: 25px; top: 17px; display: flex; gap: 6px; }
  .social span { width: 28px; height: 28px; border-radius: 50%; background: var(--white); }
  .search { position: absolute; left: 523px; top: 17px; width: 175px; height: 30px; border: 1px solid #e8e8e8; display: flex; }
  .search-field { flex: 1; background: var(--white); font-size: 12px; color: #555; line-height: 28px; padding-left: 10px; }
  .search-btn { width: 36px; display: flex; align-items: center; justify-content: center; border-left: 1px solid #e8e8e8; }
  .account { position: absolute; left: 718px; top: 21px; font-size: 12.5px; color: var(--white); }

  .intro { position: absolute; left: 0; top: 447px; width: 820px; height: 373px; background: var(--panel); }
  .intro h1 { position: absolute; left: 29px; top: 40px; font-size: 30px; color: var(--ink); letter-spacing: .3px; }
  .intro-copy { position: absolute; left: 25px; top: 87px; width: 440px; font-size: 12.3px; line-height: 22.5px; }
  .benefit { position: absolute; left: 497px; width: 305px; }
  .benefit h2 { font-size: 19px; color: var(--green-text); margin-bottom: 8px; }
  .benefit p { font-size: 12px; line-height: 17px; }

  .know { position: absolute; left: 0; top: 820px; width: 333px; height: 263px; background: var(--green); }
  .know h2 { position: absolute; left: 25px; top: 36px; font-size: 26px; color: var(--white); }
  .know ul { position: absolute; left: 28px; top: 76px; list-style: none; }
  .know li { font-size: 13px; line-height: 25.5px; color: var(--white); }

  .contact-card { position: absolute; left: 333px; top: 820px; width: 214px; height: 263px; background: var(--dark); }
  .portrait { position: absolute; left: 55px; top: 42px; width: 104px; height: 104px; border-radius: 50%; border: 2px solid #9a9a9a; background: linear-gradient(180deg, #6b7e95 0%, #2e3b4f 100%); }
  .quote-btn { position: absolute; left: 19px; top: 170px; width: 176px; height: 51px; border: 1px solid var(--white); color: var(--white); font-size: 19px; display: flex; align-items: center; justify-content: center; }

  .pitch { position: absolute; left: 547px; top: 820px; width: 273px; height: 263px; background: var(--dark-2); color: var(--white); }
  .pitch h2 { position: absolute; left: 17px; top: 60px; font-size: 18.5px; line-height: 24px; }
  .pitch p { position: absolute; left: 17px; top: 142px; width: 240px; font-size: 15px; line-height: 17px; }

  .site-footer { position: absolute; left: 0; top: 1083px; width: 820px; height: 83px; background: var(--panel); text-align: center; font-size: 12px; line-height: 18px; color: #333; padding-top: 28px; }
</style>
</head>
<body>
  <div class="backdrop-left" role="img" aria-label="World map with businessman silhouette"></div>
  <div class="backdrop-right" role="img" aria-label="World map with businessmen silhouettes"></div>

  <div class="page">
    <header class="masthead">
      <div class="nav-panel">
        <div class="brand">
          <span class="brand-dot"></span>
          <span class="brand-name">BREVARD TRADE PARTNERS</span>
        </div>
        <ul class="main-nav cond">
          <li>Home</li>
          <li>About Us</li>
          <li>Product Categories</li>
          <li>Sourcing &amp; Procurment</li>
          <li>Request Quote</li>
          <li>Clients</li>
          <li>Contact Us</li>
        </ul>
      </div>
      <div class="hero" role="img" aria-label="Photo of blue arrow signs reading outsourcing"></div>
    </header>

    <div class="toolbar">
      <div class="social"><span></span><span></span><span></span><span></span></div>
      <div class="search">
        <div class="search-field">Search Here...</div>
        <div class="search-btn">
          <svg width="16" height="16" viewBox="0 0 16 16"><circle cx="6.5" cy="6.5" r="5" fill="none" stroke="#fff" stroke-width="2"/><line x1="10.2" y1="10.2" x2="15" y2="15" stroke="#fff" stroke-width="2.2"/></svg>
        </div>
      </div>
      <div class="account">Login /&nbsp; Register</div>
    </div>

    <section class="intro">
      <h1 class="cond">BREVARD TRADE PARTNERS</h1>
      <p class="intro-copy">Lorem ipsum dolor sit amet, consectetur adipiscing elit. Praesent at tincidunt dolor, nec pulvinar elit. Vivamus imperdiet ipsum lacus, eu suscipit lacus maximus sed. Donec a posuere magna. Fusce finibus, elit nec semper convallis, odio magna feugiat nibh, eget feugiat elit nunc eu erat. Vestibulum ante ipsum primis in faucibus orci luctus et ultrices posuere cubilia Curae; Aliquam ac ipsum in mi luctus bibendum ac vitae nibh. Cras malesuada consequat dui, efficitur ultrices lectus aliquam ut. Nulla congue sollicitudin suscipit. Phasellus luctus fringilla diam convallis elementum. Curabitur quis lobortis est. Proin venenatis luctus efficitur. Nam tempor mattis nibh, id hendrerit felis malesuada ac. Aliquam sit amet urna eu nulla eleifend bibendum sed ut est. Mauris tempus sodales nibh, eget scelerisque sem viverra sed.</p>

      <div class="benefit" style="top:43px">
        <h2 class="cond">ACCESS EMERGING MARKETS</h2>
        <p>Lorem ipsum dolor sit amet, consectetur adipiscing elit. Praesent at tincidunt dolor, nec pulvinar elit. Vivamus imperdiet ipsum lacus, maximus sed.</p>
      </div>
      <div class="benefit" style="top:152px">
        <h2 class="cond">REALISE VALUE BY SOURCING DIRECT</h2>
        <p>Lorem ipsum dolor sit amet, consectetur adipiscing elit. Praesent at tincidunt dolor, nec pulvinar elit. Vivamus imperdiet ipsum lacus, maximus sed.</p>
      </div>
      <div class="benefit" style="top:257px">
        <h2 class="cond">MANAGE QUALITY AND RELIABILITY RISKS</h2>
        <p>Lorem ipsum dolor sit amet, consectetur adipiscing elit. Praesent at tincidunt dolor, nec pulvinar elit. Vivamus imperdiet ipsum lacus, maximus sed.</p>
      </div>
    </section>

    <section class="know">
      <h2 class="cond">WHAT DO YOU NEED TO KNOW</h2>
      <ul>
        <li>Contract Sewing in China</li>
        <li>What is the Process?</li>
        <li>What the Minimum Order?</li>
        <li>Contract Outsourcing FAQ</li>
        <li>Outsourcing Case Study</li>
        <li>Custom Industrial Sewing in China</li>
      </ul>
    </section>

    <section class="contact-card">
      <div class="portrait" role="img" aria-label="Portrait photo of a sourcing consultant"></div>
      <div class="quote-btn cond">REQUEST QUOTE</div>
    </section>

    <section class="pitch">
      <h2 class="cond">OUTSOURCE YOUR SEWING NEEDS TO TRUSTED CONTRACTORS IN CHINA</h2>
      <p>Please contact us for immediate consultation regarding your outsourcing project.</p>
    </section>

    <footer class="site-footer">
      © Copyright 2015, Brevard Trade Partners, LLC. All rights reserved.<br>
      Website Designed and Developed by Larkfield Studio
    </footer>
  </div>
</body>
</html>
```